Mobile welding fabrication and repair, heavy equipment and semi repair

We need a business card design that will catch the eye but look prelesional at the same time. Were based out of Idaho and we do all welding fabrication jobs and repairs, we also build and install custom pipe fences for personal or larger scale fence jobs and can give free quotes. We can do semi truck and trailer repairs Mobily also.

Target Market(s)

Welding

Industry/Entity Type

welding and repair

Contact Information for Business Card

email (ravenforgeandmend@mailbay.net, phone number 208-417-3826, owner (Dalton Whitcomb), Pipe Fence, Semi Repair, Mobile welding and fabrication

Font styles to use
Sans Serif

Requirements
Must have
• My logo in black background on one side , and other side my logo in white back round with all the information listed on card details
Nice to have
• make it stand out from other business cards

```html
<!DOCTYPE html>
<html lang="en">
<head>
<meta charset="utf-8">
<title>Ravenforge and Mend – Business Card</title>
<link rel="stylesheet" href="https://fonts.googleapis.com/css2?family=Lato:wght@400;700;900&display=swap">
<style>
  :root {
    --page-bg: #a3a3a3;
    --card-dark: #0b0b0b;
    --card-dark-glow: #2e2e2e;
    --card-light: #ffffff;
    --brand-blue: #1672c4;
    --ink: #2b2b2b;
    --rule: #b5b5b5;
  }
  * { margin: 0; padding: 0; box-sizing: border-box; }
  html, body {
    width: 1200px; height: 1200px; overflow: hidden;
    background: var(--page-bg);
    font-family: "Lato", sans-serif;
  }
  .card {
    position: absolute; top: 303px; height: 594px;
    text-align: center;
  }
  .card--front {
    left: 201px; width: 369px;
    background: radial-gradient(circle at 50% 55%, var(--card-dark-glow) 0%, #161616 40%, var(--card-dark) 85%);
  }
  .card--back {
    left: 599px; width: 364px;
    background: var(--card-light);
    color: var(--ink);
  }
  .wordmark {
    position: absolute; left: 0; right: 0;
    color: var(--brand-blue);
    font-weight: 900;
    line-height: 1;
  }
  .wordmark__main { display: block; font-size: 40px; letter-spacing: 1px; }
  .wordmark__sub { display: block; font-size: 20px; letter-spacing: 3px; margin-top: 8px; }
  .card--front .wordmark { top: 258px; }
  .card--back .wordmark { top: 155px; }

  .contact { position: absolute; left: 0; right: 0; top: 356px; }
  .contact__name { font-size: 22px; font-weight: 700; color: var(--brand-blue); line-height: 1; }
  .contact__role { font-size: 16px; margin-top: 10px; line-height: 1; }
  .rule { width: 72px; height: 1px; background: var(--rule); margin: 17px auto 0; }
  .contact__phone { font-size: 16px; margin-top: 16px; line-height: 1; }
  .contact__email { font-size: 15.5px; margin-top: 7px; line-height: 1; }
  .services { margin-top: 18px; font-size: 14.5px; line-height: 27px; }
  .services__dot {
    display: inline-block; width: 9px; height: 9px; border-radius: 50%;
    background: var(--brand-blue); margin: 0 5px; vertical-align: 2px;
  }
</style>
</head>
<body>
  <section class="card card--front" role="img" aria-label="Dark card face with faint spark burst pattern behind the company name">
    <div class="wordmark">
      <span class="wordmark__main">RAVENFORGE</span>
      <span class="wordmark__sub">AND MEND</span>
    </div>
  </section>

  <section class="card card--back">
    <div class="wordmark">
      <span class="wordmark__main">RAVENFORGE</span>
      <span class="wordmark__sub">AND MEND</span>
    </div>
    <div class="contact">
      <p class="contact__name">DALTON WHITCOMB</p>
      <p class="contact__role">OWNER</p>
      <div class="rule"></div>
      <p class="contact__phone">208-417-3826</p>
      <p class="contact__email">ravenforgeandmend@mailbay.net</p>
      <div class="rule"></div>
      <div class="services">
        <p>FABRICATION<span class="services__dot"></span>MOBILE WELDING</p>
        <p>SEMI REPAIR<span class="services__dot"></span>PIPE FENCE</p>
      </div>
    </div>
  </section>
</body>
</html>
```